Velorum Kinetics Business Card Contest

Velorum Kinetics is a b-b blockchain technology solutions company. We are seeking a professional yet minimalist business card to be designed. We would like the business card:1) to have a QR code to our website (velorum-k.example) somewhere on the card2) Colour/design to be somewhat relevant to our website (refer to attached image)3) Elegant-looking 4) No irrelevant iconsYou should use these information:Name: Eric BarbierDesignation: CEOPhone: +65 9752 2604Email: eric@triple-a.ioAddress: Singapore | China

```html
<!DOCTYPE html>
<html lang="en">
<head>
<meta charset="utf-8">
<title>Velorum Kinetics Business Card</title>
<link href="https://fonts.googleapis.com/css2?family=Lato:wght@400;700&family=Michroma&display=swap" rel="stylesheet">
<style>
  :root {
    --backdrop: #8a5a36;
    --kraft-light: #dcbb90;
    --kraft-mid: #c79d6c;
    --kraft-dark: #b88c5c;
    --ink: #1c140e;
  }
  * { margin: 0; padding: 0; box-sizing: border-box; }
  html, body { width: 1200px; height: 900px; overflow: hidden; }
  body {
    background: var(--backdrop);
    position: relative;
    font-family: "Lato", sans-serif;
    color: var(--ink);
  }
  .card {
    position: absolute;
    left: 330px;
    width: 557px;
    height: 343px;
    background: radial-gradient(ellipse at 35% 15%, var(--kraft-light) 0%, var(--kraft-mid) 55%, var(--kraft-dark) 100%);
    box-shadow: 3px 4px 6px rgba(0,0,0,0.45);
  }
  .card-back { top: 90px; }
  .card-front { top: 470px; }

  .contact-block {
    position: absolute;
    left: 0; right: 0;
    top: 88px;
    text-align: center;
  }
  .person-name {
    font-family: "Michroma", sans-serif;
    font-size: 17px;
    letter-spacing: 0.5px;
    line-height: 24px;
  }
  .person-role {
    font-size: 14px;
    line-height: 18px;
  }
  .divider {
    width: 142px;
    height: 1px;
    background: var(--ink);
    margin: 8px auto 9px;
  }
  .contact-list { list-style: none; font-size: 15px; line-height: 20px; }
  .contact-list b { font-weight: 700; }
  .locations { font-size: 15px; line-height: 20px; margin-top: 1px; }

  .brand {
    position: absolute;
    left: 0; right: 0;
    top: 150px;
    display: flex;
    justify-content: center;
    align-items: center;
    gap: 18px;
  }
  .brand-name {
    font-family: "Michroma", sans-serif;
    font-size: 30px;
    letter-spacing: 2px;
    line-height: 40px;
    color: var(--ink);
  }
  .brand-dot {
    width: 18px; height: 18px;
    border-radius: 50%;
    background: var(--ink);
  }
</style>
</head>
<body>
  <section class="card card-back">
    <div class="contact-block">
      <h1 class="person-name">DANIEL OSGOOD</h1>
      <p class="person-role">CEO</p>
      <div class="divider"></div>
      <ul class="contact-list">
        <li><b>P:</b> +65 8316 4079</li>
        <li><b>E:</b> daniel@velorum-k.example</li>
        <li><b>W:</b> www.velorum-k.example</li>
      </ul>
      <div class="divider"></div>
      <p class="locations">Singapore | China</p>
    </div>
  </section>

  <section class="card card-front">
    <div class="brand">
      <span class="brand-name">VELORUM KINETICS</span>
      <span class="brand-dot"></span>
    </div>
  </section>
</body>
</html>
```